Design NEW business card

We would like a business card using the colour deep red wine or dark navy blue textured background (patterned or not, open to suggestions) with a high gloss debossed rose gold/copper RM Roland Mercer Jewellery business name (Provided). I have included images for your review we would like to keep our currently logo and business name on the front but you can change the layout and positioning. For the back of the card we are open to all suggestions/variations.
Business
Use our current RM Roland Mercer Jewellery logo (Provided image)

```html
<!DOCTYPE html>
<html lang="en">
<head>
<meta charset="utf-8">
<title>Roland Mercer Jewellery – Business Card</title>
<link href="https://fonts.googleapis.com/css2?family=Montserrat:wght@400&family=Open+Sans:wght@400&display=swap" rel="stylesheet">
<style>
  :root {
    --stage: #9d9d9d;
    --wine: #571c24;
    --wine-light: #652630;
    --wine-dark: #4b161d;
    --rose: #b4587d;
    --rose-light: #d88fb0;
    --ink: #3b1218;
  }
  html, body {
    margin: 0;
    padding: 0;
    width: 1200px;
    height: 1200px;
    overflow: hidden;
    background: var(--stage);
  }
  .canvas {
    position: relative;
    width: 1200px;
    height: 1200px;
  }
  .card {
    position: absolute;
    width: 573px;
    height: 326px;
    background: var(--wine);
    overflow: hidden;
  }
  .card--front { left: 310px; top: 227px; }
  .card--back  { left: 309px; top: 638px; }

  .card__texture {
    position: absolute;
    inset: 0;
    background:
      radial-gradient(ellipse at 50% 40%, var(--wine-light) 0%, var(--wine) 55%, var(--wine-dark) 100%);
  }

  .brand-mark {
    position: absolute;
    width: 56px;
    height: 56px;
    border-radius: 50%;
    background: radial-gradient(circle at 35% 30%, var(--rose-light) 0%, var(--rose) 60%, #8f3a5e 100%);
  }
  .card--front .brand-mark { left: 130px; top: 150px; }
  .card--back .brand-mark  { left: 130px; top: 141px; }

  .brand {
    position: absolute;
    color: var(--rose);
    font-family: "Montserrat", sans-serif;
    font-weight: 400;
    text-transform: uppercase;
  }
  .brand__name {
    display: block;
    font-size: 21px;
    letter-spacing: 0.22em;
    line-height: 1;
    white-space: nowrap;
  }
  .brand__line {
    display: block;
    margin-top: 10px;
    font-size: 8px;
    letter-spacing: 2.9em;
    line-height: 1;
    white-space: nowrap;
  }
  .card--front .brand { left: 196px; top: 200px; }
  .card--back .brand  { left: 196px; top: 191px; }

  .holder {
    position: absolute;
    left: 37px;
    top: 258px;
    color: var(--ink);
    font-family: "Open Sans", sans-serif;
  }
  .holder__name { font-size: 14px; line-height: 18px; }
  .holder__role { font-size: 11px; line-height: 16px; }

  .contact {
    position: absolute;
    right: 45px;
    top: 239px;
    margin: 0;
    padding: 0;
    list-style: none;
    text-align: right;
    color: var(--ink);
    font-family: "Open Sans", sans-serif;
    font-size: 10.5px;
    line-height: 19.5px;
  }
</style>
</head>
<body>
<main class="canvas">
  <section class="card card--front" aria-label="Card front">
    <div class="card__texture" role="img" aria-label="Subtle tone-on-tone curved line pattern on deep wine paper"></div>
    <div class="brand-mark" aria-hidden="true"></div>
    <div class="brand">
      <span class="brand__name">Roland Mercer</span>
      <span class="brand__line">Jewellery</span>
    </div>
  </section>

  <section class="card card--back" aria-label="Card back">
    <div class="card__texture" role="img" aria-label="Subtle tone-on-tone curved line pattern on deep wine paper"></div>
    <div class="brand-mark" aria-hidden="true"></div>
    <div class="brand">
      <span class="brand__name">Roland Mercer</span>
      <span class="brand__line">Jewellery</span>
    </div>
    <div class="holder">
      <div class="holder__name">Your Full Name</div>
      <div class="holder__role">Designation</div>
    </div>
    <ul class="contact">
      <li>(02)+ 98-765-432</li>
      <li>info@rmjewelers.com</li>
      <li>www.rmjewelers.com</li>
    </ul>
  </section>
</main>
</body>
</html>
```